Business Cards - Brightpath Horizon

need to design unique business card for my mortgage business. I need to design credit card style business card for my business or any unique idea that you might have

Target Market(s)

Home Loan customers

Industry/Entity Type

Mortgage Brokerage

Contact Information for Business Card

please design credit card style or very unique style business card

Colors

Designer to choose colors to be used in the design.

Requirements
Must have
• Name
• position
• Phone number
• fax number
• email address
• website address
• social media address
• All above fields will be provided once design in finalised

```html
<!DOCTYPE html>
<html lang="en">
<head>
<meta charset="utf-8">
<title>Brightpath Horizon – Business Card</title>
<link rel="stylesheet" href="https://fonts.googleapis.com/css2?family=Tinos:ital,wght@0,400;0,700;1,400&family=Orbitron:wght@500&display=swap">
<style>
  :root {
    --backdrop: #e6e8ec;
    --card: #ffffff;
    --ink-blue: #1b2f9c;
    --digit-blue: #1a3cb8;
    --accent-orange: #f29a1f;
    --body-grey: #3d3d3d;
  }
  * { box-sizing: border-box; margin: 0; padding: 0; }
  html, body {
    width: 1200px; height: 901px; overflow: hidden;
    background: var(--backdrop);
  }
  .card {
    position: absolute; left: 80px; top: 122px;
    width: 1040px; height: 656px;
    background: var(--card);
    border-radius: 34px;
    box-shadow: 0 14px 40px rgba(20, 30, 60, 0.18);
    font-family: "Tinos", "Times New Roman", serif;
  }
  .social-links {
    position: absolute; left: 45px; top: 82px;
    display: flex; gap: 5px;
  }
  .social-dot {
    width: 44px; height: 44px; border-radius: 50%;
    background: var(--ink-blue);
  }
  .brand {
    position: absolute; right: 58px; top: 92px;
    text-align: right;
  }
  .brand-name {
    display: flex; align-items: center; justify-content: flex-end; gap: 14px;
    color: var(--ink-blue);
    font-size: 50px; font-weight: 400; line-height: 1;
  }
  .brand-mark {
    width: 22px; height: 22px; border-radius: 50%;
    background: var(--accent-orange);
  }
  .tagline {
    margin-top: 12px;
    color: var(--accent-orange);
    font-style: italic; font-size: 23px;
  }
  .card-number {
    position: absolute; left: 61px; top: 338px;
    color: var(--digit-blue);
    font-family: "Orbitron", "Courier New", monospace;
    font-weight: 500; font-size: 56px; letter-spacing: 3px;
    word-spacing: 14px; white-space: nowrap;
  }
  .holder {
    position: absolute; left: 61px; top: 498px;
  }
  .holder-name {
    color: var(--ink-blue); font-size: 38px; line-height: 1.1;
  }
  .holder-role {
    color: var(--accent-orange); font-size: 30px; line-height: 1.35;
  }
  .contact {
    position: absolute; left: 363px; top: 502px;
    color: var(--body-grey); font-size: 27px; line-height: 1.42;
  }
  .contact .label { color: var(--ink-blue); font-weight: 700; }
  .address {
    position: absolute; left: 669px; top: 506px;
    color: var(--body-grey); font-size: 27px; line-height: 1.42;
  }
  .rule {
    position: absolute; left: 61px; top: 594px;
    width: 930px; height: 3px;
    background: var(--accent-orange);
  }
  .website {
    position: absolute; left: 61px; top: 604px;
    color: var(--ink-blue); font-size: 26px;
  }
</style>
</head>
<body>
  <main class="card">
    <div class="social-links" aria-label="Social media">
      <span class="social-dot"></span>
      <span class="social-dot"></span>
      <span class="social-dot"></span>
      <span class="social-dot"></span>
    </div>

    <div class="brand">
      <div class="brand-name"><span class="brand-mark"></span>Brightpath Horizon</div>
      <div class="tagline">Smart loans, Steady homes</div>
    </div>

    <div class="card-number">5172 0364 8819</div>

    <div class="holder">
      <div class="holder-name">MARCUS HALE</div>
      <div class="holder-role">CEO/FOUNDER</div>
    </div>

    <div class="contact">
      <div><span class="label">P:</span> 504 218 7365</div>
      <div>mhale@bphorizon.com</div>
    </div>

    <div class="address">
      <div>2143 Willow Crest Drive</div>
      <div>Cedar Falls, Oregon 97410</div>
    </div>

    <div class="rule"></div>
    <div class="website">www.bphorizon.com</div>
  </main>
</body>
</html>
```